Law firm business card

Information:

Me Mireille Dufontaine

website: dufontaine-legal.ca
email: mireille@dufontaine-legal.ca
Phone: 514 382-5167
Fax: 514 382-5169

Address:
Dufontaine and associates
2719 Belcourtier
Montreal, QC
H2K 3M9

Areas of Expertise:
Franchise Agreements, Financing, Acquisition, Real Estate Development, Commercial Agreements and Corporate Law

Target Market(s)

executives, companie managers

Industry/Entity Type

Business

Colors
f78f20
000000

Requirements
Must have
• Must use the logo, the logo is available here:

https://www.filecrate-example.com/sh/qyt3kwud82mfa0x/BBQTn7Lhvpe_kRTXwJM_GhcYb

```html
<!DOCTYPE html>
<html lang="en">
<head>
<meta charset="utf-8">
<title>Dufontaine &amp; Associates – Business Card</title>
<link rel="stylesheet" href="https://fonts.googleapis.com/css2?family=Josefin+Sans:wght@400;600;700&display=swap">
<style>
  :root {
    --orange: #f78f20;
    --ink: #000000;
    --slate: #4f5660;
    --paper: #ffffff;
    --paper-shade: #eeeff0;
    --icon-bg: #c6d43a;
    --backdrop: #e4e4e2;
    --white: #ffffff;
  }
  * { box-sizing: border-box; margin: 0; padding: 0; }
  html, body {
    width: 1200px; height: 896px; overflow: hidden;
    background: var(--backdrop);
    font-family: "Josefin Sans", Arial, sans-serif;
  }
  .sheet {
    width: 1200px; height: 896px;
    display: flex; flex-direction: column; align-items: center; justify-content: center;
    gap: 32px;
  }
  .card {
    position: relative;
    width: 700px; height: 400px;
    background: linear-gradient(135deg, var(--paper) 0%, var(--paper) 55%, var(--paper-shade) 100%);
    box-shadow: 0 4px 14px rgba(0,0,0,0.12);
    overflow: hidden;
  }

  /* Brand name (set as plain text) */
  .brand-name {
    color: var(--orange);
    font-weight: 600;
    text-transform: uppercase;
    line-height: 1.05;
    text-align: center;
    white-space: nowrap;
  }
  .brand-name span { display: block; }

  /* Front */
  .card-front .brand-name {
    position: absolute; left: 0; right: 0; top: 138px;
    font-size: 44px; letter-spacing: 2px;
  }
  .card-front .brand-name span { font-size: 32px; letter-spacing: 3px; margin-top: 4px; }
  .front-rule {
    position: absolute; left: 0; right: 0; bottom: 40px; height: 9px;
    background: var(--slate);
  }
  .front-band {
    position: absolute; left: 0; right: 0; bottom: 0; height: 32px;
    background: var(--orange);
  }

  /* Back */
  .card-back .brand-name {
    position: absolute; left: 0; width: 385px; top: 160px;
    font-size: 36px; letter-spacing: 1px;
  }
  .card-back .brand-name span { font-size: 26px; letter-spacing: 2px; margin-top: 4px; }
  .contact-panel {
    position: absolute; top: 0; right: 0; bottom: 0; width: 315px;
    background: var(--orange);
    color: var(--white);
    padding: 50px 16px 0 30px;
  }
  .contact-name {
    font-size: 18px; font-weight: 700; letter-spacing: 1.5px; text-transform: uppercase;
    white-space: nowrap;
  }
  .contact-title {
    font-size: 11px; letter-spacing: 2px; text-transform: uppercase; margin-top: 5px;
  }
  .contact-address {
    font-size: 15px; line-height: 1.5; margin-top: 40px;
  }
  .contact-list { list-style: none; margin-top: 18px; }
  .contact-list li {
    display: flex; align-items: center; gap: 12px;
    font-size: 14px; margin-bottom: 11px;
    white-space: nowrap;
  }
  .contact-icon {
    width: 20px; height: 20px; flex: none;
    background: var(--icon-bg); border-radius: 3px;
    display: flex; align-items: center; justify-content: center;
  }
</style>
</head>
<body>
<main class="sheet">

  <section class="card card-front" aria-label="Card front">
    <p class="brand-name">Dufontaine<span>&amp; Associates</span></p>
    <div class="front-rule"></div>
    <div class="front-band"></div>
  </section>

  <section class="card card-back" aria-label="Card back">
    <p class="brand-name">Dufontaine<span>&amp; Associates</span></p>

    <div class="contact-panel">
      <h1 class="contact-name">Mireille Dufontaine</h1>
      <p class="contact-title">General Manager</p>
      <p class="contact-address">2719 Belcourtier<br>Montreal, QC H2K 3M9</p>
      <ul class="contact-list">
        <li>
          <span class="contact-icon">
            <svg width="12" height="12" viewBox="0 0 12 12" aria-hidden="true"><path d="M3 1 L5 3.5 L4 5 Q5.5 7 7 8 L8.5 7 L11 9 L9.5 11 Q4 10 1 2.5 Z" fill="#fff"/></svg>
          </span>
          514 382-5167
        </li>
        <li>
          <span class="contact-icon">
            <svg width="12" height="12" viewBox="0 0 12 12" aria-hidden="true"><rect x="3" y="1" width="6" height="3" fill="#fff"/><rect x="1" y="5" width="10" height="4" rx="1" fill="#fff"/><rect x="3" y="8" width="6" height="3" fill="#fff"/></svg>
          </span>
          514 382-5169
        </li>
        <li>
          <span class="contact-icon">
            <svg width="12" height="12" viewBox="0 0 12 12" aria-hidden="true"><rect x="1" y="2.5" width="10" height="7" fill="#fff"/><path d="M1 2.5 L6 6.5 L11 2.5" fill="none" stroke="#c6d43a" stroke-width="1"/></svg>
          </span>
          mireille@dufontaine-legal.ca
        </li>
        <li>
          <span class="contact-icon">
            <svg width="12" height="12" viewBox="0 0 12 12" aria-hidden="true"><circle cx="6" cy="6" r="4.5" fill="none" stroke="#fff" stroke-width="1.2"/><path d="M1.5 6 H10.5 M6 1.5 Q3.5 6 6 10.5 M6 1.5 Q8.5 6 6 10.5" fill="none" stroke="#fff" stroke-width="1"/></svg>
          </span>
          dufontaine-legal.ca
        </li>
      </ul>
    </div>
  </section>

</main>
</body>
</html>
```